Business Card design which attached logo. Company is called Crestline Shield and main colours are Orange & Black.

Company specialises in Paint Protection and Detailing for supercars.

Details needed on business card:

Sales

Address: Unit 14, 517 Hadley Road, Fernvale Heights, NSW 2200

Phone: 02 6194 2738

website: www.crestlineshield.com.au

Email: sales@crestlineshield.com.au

```html
<!DOCTYPE html>
<html lang="en">
<head>
<meta charset="utf-8">
<title>Crestline Shield – Business Cards</title>
<link href="https://fonts.googleapis.com/css2?family=Lato:wght@300;400&display=swap" rel="stylesheet">
<style>
  :root {
    --bg: #1d1e21;
    --card-black: #0b0b0c;
    --orange: #f05a24;
    --orange-light: #f4762f;
    --orange-text: #e4652a;
    --name-grey: #d9d9d9;
    --icon-white: #f2f2f2;
  }
  * { margin: 0; padding: 0; box-sizing: border-box; }
  html, body {
    width: 1200px; height: 900px; overflow: hidden;
    background: var(--bg);
    font-family: "Lato", Arial, sans-serif;
  }
  .stage { position: relative; width: 1200px; height: 900px; }

  .card {
    position: absolute;
    background: var(--card-black);
    border-radius: 4px;
    box-shadow: 0 18px 40px rgba(0,0,0,.55);
    overflow: hidden;
  }

  /* Company name: plain text with one plain circle */
  .company-name {
    display: flex; align-items: center; gap: 12px;
    color: var(--orange-text);
    font-weight: 300; font-size: 24px; letter-spacing: 1px;
    text-transform: uppercase; white-space: nowrap;
  }
  .company-name .mark-dot {
    width: 14px; height: 14px; border-radius: 50%;
    background: var(--orange-text); flex: none;
  }

  /* Front card */
  .card-front { left: 110px; top: 140px; width: 360px; height: 620px; }
  .card-front .company-name { position: absolute; left: 36px; top: 52px; }
  .person-name {
    position: absolute; left: 36px; top: 118px;
    color: var(--name-grey);
    font-weight: 300; font-size: 30px; letter-spacing: 1px;
    text-transform: uppercase; white-space: nowrap;
  }
  .address {
    position: absolute; left: 36px; top: 172px;
    color: var(--orange-text);
    font-weight: 300; font-size: 13.5px; line-height: 1.45;
  }
  .contact-list {
    position: absolute; left: 36px; top: 228px;
    list-style: none;
  }
  .contact-list li {
    display: flex; align-items: center; gap: 10px;
    color: var(--orange-text);
    font-weight: 300; font-size: 13.5px; line-height: 24px;
    white-space: nowrap;
  }
  .contact-list svg { width: 13px; height: 13px; flex: none; }

  .dome { position: absolute; left: 0; bottom: 0; width: 360px; height: 290px; }

  /* Back card */
  .card-back { left: 520px; top: 270px; width: 600px; height: 360px; }
  .car-outline-area {
    position: absolute; left: 70px; top: 50px; width: 460px; height: 170px;
    border-radius: 80px 120px 40px 40px;
    background: radial-gradient(ellipse at center, rgba(240,90,36,.22), rgba(240,90,36,0) 70%);
  }
  .card-back .company-name {
    position: absolute; left: 0; right: 0; top: 248px;
    justify-content: center;
  }
</style>
</head>
<body>
<main class="stage">

  <section class="card card-front" aria-label="Business card front">
    <div class="company-name"><span class="mark-dot" aria-hidden="true"></span>Crestline Shield</div>
    <div class="person-name">Daniel Harper</div>
    <p class="address">Unit 14, 517 Hadley Road,<br>Fernvale Heights, NSW 2200</p>
    <ul class="contact-list">
      <li>
        <svg viewBox="0 0 16 16" aria-hidden="true"><path fill="var(--icon-white)" d="M4 1l2.5 3-1.5 2c1 2 2.5 3.5 4.5 4.5l2-1.5 3 2.5-1.5 2.5C7 14 2 9 1.5 2.5z"/></svg>
        02 6194 2738
      </li>
      <li>
        <svg viewBox="0 0 16 16" aria-hidden="true"><rect x="1" y="3" width="14" height="10" fill="var(--icon-white)"/><path d="M1 3l7 6 7-6" fill="none" stroke="var(--card-black)" stroke-width="1.3"/></svg>
        sales@crestlineshield.com.au
      </li>
      <li>
        <svg viewBox="0 0 16 16" aria-hidden="true"><circle cx="8" cy="8" r="6.5" fill="none" stroke="var(--icon-white)" stroke-width="1.4"/><path d="M1.5 8h13M8 1.5c-3 3.5-3 9.5 0 13M8 1.5c3 3.5 3 9.5 0 13" fill="none" stroke="var(--icon-white)" stroke-width="1.1"/></svg>
        www.crestlineshield.com.au
      </li>
    </ul>
    <svg class="dome" viewBox="0 0 360 290" role="img" aria-label="Orange dome with a white line sketch of a supercar seen from above">
      <defs>
        <linearGradient id="domeFill" x1="0" y1="0" x2="0" y2="1">
          <stop offset="0" stop-color="var(--orange-light)"/>
          <stop offset="1" stop-color="var(--orange)"/>
        </linearGradient>
      </defs>
      <path d="M0 290 V180 A180 180 0 0 1 360 180 V290 Z" fill="url(#domeFill)"/>
      <path d="M40 150 A150 150 0 0 1 250 30" fill="none" stroke="#fff" stroke-width="5" stroke-linecap="round" opacity=".9"/>
    </svg>
  </section>

  <section class="card card-back" aria-label="Business card back">
    <div class="car-outline-area" role="img" aria-label="Orange line sketch of a supercar in side profile"></div>
    <div class="company-name"><span class="mark-dot" aria-hidden="true"></span>Crestline Shield</div>
  </section>

</main>
</body>
</html>
```